Bramwell Policy Lookout Hub

I want a landing page for them to click on the logo with a brief description of the site.

Once they click on the logo, it will take them to make a decision for two types of insurance. One will be health and the other will be home/auto.

I will need an iframe for the home/auto and it will take them to a site (which is already built) for them to get a quote.

I will need a separate iframe for the health to take them to separate site (which is built) for them to get a quote.

Target Market(s)

18-45 Year olds who want to go online for insurance quotes. This is for quoting primarily and not an information site.

Industry/Entity Type

Health

Requirements
Must have
• Sleek and sexy. I have a logo as well.

May want the following on the landing page:
Georgia's FIRST Insurance Exchange for Home, Auto, and Health Insurance

No Hassle, Real-time, Quotes - As a Matter of fact... You call us if interested, We dont sell your information and Most Importantly… its free!!

Give it a shot… Click on the logo to get started and if you are interested in one of the many carriers we represent, call us.
Should not have
• Don't want the typical website. I want this to be different than all template boxes.

```html
<!DOCTYPE html>
<html lang="en">
<head>
<meta charset="utf-8">
<title>Bramwell Policy Lookout Hub</title>
<link rel="stylesheet" href="https://fonts.googleapis.com/css2?family=Oswald:wght@500&family=Gelasio:wght@400;700&family=Ubuntu:wght@400&display=swap">
<style>
  :root {
    --nav-top: #d0182c;
    --nav-bottom: #7e0a18;
    --nav-divider: #e23a4c;
    --nav-divider-dark: #6a0614;
    --ink: #1b2d55;
    --accent-deep: #c11a2c;
    --accent-bright: #ee1326;
    --brand-blue: #1f8fd6;
    --house-red: #cc1b2c;
    --car-blue: #3a7fd4;
    --road-grey: #4a4a4a;
    --ghost-grey: #e6e6e6;
    --footer-top: #23414f;
    --footer-bottom: #0a1a24;
    --paper: #ffffff;
  }
  * { box-sizing: border-box; margin: 0; padding: 0; }
  html, body {
    width: 1200px;
    height: 673px;
    overflow: hidden;
    background: var(--paper);
  }
  .page {
    position: relative;
    width: 1200px;
    height: 673px;
  }
  .site-nav {
    position: absolute;
    left: 0; top: 0;
    width: 1200px;
    height: 78px;
    background: linear-gradient(to bottom, var(--nav-top), var(--nav-bottom));
    display: flex;
  }
  .site-nav a {
    display: flex;
    align-items: center;
    height: 100%;
    color: #fff;
    text-decoration: none;
    font-family: "Oswald", sans-serif;
    font-weight: 500;
    font-size: 24px;
    letter-spacing: 0.3px;
    text-transform: uppercase;
  }
  .nav-home { width: 156px; padding-left: 22px; border-right: 1px solid var(--nav-divider-dark); }
  .nav-quote { width: 223px; padding-left: 43px; border-left: 1px solid var(--nav-divider); border-right: 1px solid var(--nav-divider-dark); }
  .nav-contact { padding-left: 37px; border-left: 1px solid var(--nav-divider); }

  .brand-mark {
    position: absolute;
    left: 30px;
    top: 120px;
    width: 413px;
    height: 383px;
    display: flex;
    flex-direction: column;
    align-items: center;
    justify-content: center;
    gap: 22px;
    text-decoration: none;
  }
  .brand-dot {
    width: 60px;
    height: 60px;
    border-radius: 50%;
    background: var(--brand-blue);
  }
  .brand-name {
    font-family: "Gelasio", serif;
    font-weight: 700;
    font-size: 44px;
    line-height: 1.15;
    text-align: center;
    color: var(--brand-blue);
  }

  .cover-icon { position: absolute; }
  .icon-home {
    left: 503px; top: 120px; width: 156px; height: 102px;
    background: var(--house-red);
    border-radius: 4px;
  }
  .icon-auto {
    left: 764px; top: 134px; width: 233px; height: 91px;
    background: linear-gradient(to right, var(--car-blue), var(--road-grey));
    border-radius: 4px;
  }
  .icon-health {
    left: 1060px; top: 132px; width: 62px; height: 98px;
    background: var(--ghost-grey);
    border-radius: 30px 30px 8px 8px;
  }

  .intro {
    position: absolute;
    left: 515px;
    top: 272px;
    width: 670px;
    font-family: "Gelasio", serif;
    font-size: 20px;
    line-height: 25px;
    color: var(--ink);
  }
  .intro p + p { margin-top: 26px; }
  .intro .free { color: var(--accent-deep); }
  .intro .cta { color: var(--accent-bright); }

  .site-footer {
    position: absolute;
    left: 0; bottom: 0;
    width: 1200px;
    height: 66px;
    background: linear-gradient(to bottom, var(--footer-top), var(--footer-bottom));
    display: flex;
    align-items: center;
    justify-content: center;
    font-family: "Ubuntu", sans-serif;
    font-size: 18px;
    color: #fff;
  }
</style>
</head>
<body>
<div class="page">
  <nav class="site-nav">
    <a class="nav-home" href="#">Home Page</a>
    <a class="nav-quote" href="#">Quote Request</a>
    <a class="nav-contact" href="#">Contact Us</a>
  </nav>

  <a class="brand-mark" href="#">
    <span class="brand-dot"></span>
    <span class="brand-name">Bramwell Policy<br>Lookout Hub</span>
  </a>

  <div class="cover-icon icon-home" role="img" aria-label="Home insurance icon: red house"></div>
  <div class="cover-icon icon-auto" role="img" aria-label="Auto insurance icon: blue car on a road"></div>
  <div class="cover-icon icon-health" role="img" aria-label="Health insurance icon: faint grey person outline"></div>

  <section class="intro">
    <p>Georgia's FIRST Insurance Exchange for Home, Auto, and Health Insurance</p>
    <p>No Hassle, Real-time, Quotes - As a Matter of fact... You call us if interested, We dont sell your information and Most Importantly... <span class="free">ITS FREE!!</span></p>
    <p>Give it a shot... <span class="cta">CLICK ON THE LOGO TO GET STARTED</span> and if you are interested in one of the many carriers we represent, call us.</p>
  </section>

  <footer class="site-footer">© 2013, All Rights Reserved,&nbsp; bramwellhub.com</footer>
</div>
</body>
</html>
```